3 Page Design for Ninth Bay Capital

We want a Home Page, About Page, and Products & Services Page for Ninth Bay Capital. Please refer to the attached docs for more info.
If done in Figma, would like Figma files that can easily be ported to Wordpress.

```html
<!DOCTYPE html>
<html lang="en">
<head>
<meta charset="UTF-8">
<title>Ninth Bay Capital — Home</title>
<link href="https://fonts.googleapis.com/css2?family=Red+Hat+Display:wght@400;500;600;700;800&display=swap" rel="stylesheet">
<style>
  :root{
    --cream:#f8f3ec;
    --sand:#efe3d3;
    --bronze:#8b7355;
    --bronze-dark:#7a6347;
    --line:#7d6647;
    --ink:#2f2f2f;
    --text:#3d3d3d;
    --purple:#6a5a96;
    --crimson:#a11d33;
    --card:#2d2d2d;
    --white:#ffffff;
    --pale-label:#e3d5bf;
    --grey-label:#6b6b6b;
  }
  *{margin:0;padding:0;box-sizing:border-box}
  html,body{width:1200px;height:4227px;overflow:hidden}
  body{position:relative;background:var(--white);font-family:"Red Hat Display",sans-serif;color:var(--text)}
  .abs{position:absolute}

  /* header */
  .site-header{position:absolute;left:0;top:0;width:1200px;height:75px;background:var(--white);z-index:3}
  .nav-link{position:absolute;top:29px;font-size:14px;color:#444;letter-spacing:.2px}
  .nav-link.active{color:var(--bronze);font-weight:600}
  .btn-quote{position:absolute;left:998px;top:21px;width:112px;height:33px;background:var(--crimson);color:var(--white);font-size:12px;font-weight:700;border-radius:4px;display:flex;align-items:center;justify-content:center}
  .brand-tab{position:absolute;left:465px;top:0;width:272px;height:144px;background:var(--white);border-radius:0 0 30px 30px;z-index:4;text-align:center}
  .brand-tab .brand-dot{width:60px;height:60px;border-radius:50%;background:var(--bronze);margin:14px auto 10px}
  .brand-name{font-weight:800;color:var(--ink);font-size:20px;letter-spacing:.5px}
  .brand-tag{font-size:7px;letter-spacing:2.5px;color:var(--bronze);margin-top:3px}

  /* hero */
  .hero{position:absolute;left:0;top:75px;width:1200px;height:595px;background:var(--sand)}
  .hero-photo{position:absolute;left:635px;top:0;width:565px;height:595px;background:linear-gradient(120deg,#2a211b 0%,#6b4a33 40%,#c9b39a 65%,#3a2c22 100%)}
  .hero h1{position:absolute;left:110px;top:168px;font-size:48px;line-height:60px;font-weight:800;color:var(--ink);letter-spacing:-.5px}
  .hero .eyebrow{position:absolute;left:110px;top:303px;font-size:15px;letter-spacing:2.5px;color:var(--bronze);font-weight:500}
  .hero p{position:absolute;left:110px;top:330px;width:480px;font-size:15px;line-height:29px;color:var(--ink)}
  .btn-strategy{position:absolute;left:112px;top:437px;width:218px;height:51px;background:var(--purple);color:var(--white);font-size:14px;font-weight:700;border-radius:4px;display:flex;align-items:center;justify-content:center}

  /* intro */
  .intro{position:absolute;left:0;top:670px;width:1200px;height:843px;background:var(--cream)}
  .intro-lead{position:absolute;left:110px;top:88px;width:990px;font-size:36px;line-height:60px;color:var(--bronze);font-weight:500}
  .intro-lead strong{font-weight:700}
  .pillars{position:absolute;left:0;top:420px;width:1200px;height:400px}
  .pillar{position:absolute;top:0;width:240px;text-align:center}
  .pillar svg.icon{display:block;margin:74px auto 0}
  .pillar h3{font-size:27px;font-weight:500;color:var(--bronze);margin-top:12px}
  .pillar p{font-size:16px;line-height:30px;color:var(--ink);margin-top:10px}

  /* services */
  .services{position:absolute;left:0;top:1513px;width:1200px;height:1061px;background:var(--bronze)}
  .section-title{position:absolute;left:0;width:1200px;text-align:center;font-weight:800;font-size:46px;letter-spacing:-.5px}
  .section-kicker{position:absolute;left:0;width:1200px;text-align:center;font-size:15px;letter-spacing:6px;font-weight:500}
  .service-row{position:absolute;left:0;width:1200px}
  .service-row.highlight{background:var(--bronze-dark);width:778px}
  .service-num{position:absolute;left:107px;font-size:68px;font-weight:700;color:var(--white)}
  .service-name{position:absolute;left:309px;font-size:27px;font-weight:700;color:var(--white)}
  .service-copy{position:absolute;left:309px;font-size:17px;line-height:33px;color:var(--white)}
  .rule{position:absolute;left:110px;width:972px;height:1px;background:rgba(255,255,255,.35)}
  .service-photo{position:absolute;left:778px;top:363px;width:310px;height:281px;border-radius:0 22px 0 0;background:linear-gradient(135deg,#d8cfc4,#f2eee8 55%,#bdb3a6)}
  .btn-more{position:absolute;left:530px;top:943px;width:140px;height:49px;background:var(--crimson);color:var(--white);font-size:15px;font-weight:700;border-radius:4px;display:flex;align-items:center;justify-content:center}

  /* visual story */
  .story{position:absolute;left:0;top:2574px;width:1200px;height:1110px;background:var(--cream)}
  .story p.lead{position:absolute;left:190px;top:180px;width:820px;text-align:center;font-size:14.5px;line-height:29px;color:var(--text)}
  .story-mark{position:absolute;left:399px;top:346px;width:400px;height:400px;border-radius:50%;background:#ebe6df;display:flex;align-items:center;justify-content:center;font-weight:800;font-size:30px;letter-spacing:1px;color:#d6cfc5}
  .story-label{position:absolute;font-size:21px;font-weight:700}
  .story-desc{position:absolute;font-size:21px;line-height:33px;color:var(--bronze)}
  .right{text-align:right}

  /* cta */
  .cta{position:absolute;left:112px;top:3510px;width:976px;height:397px;background:var(--card);border-radius:30px}
  .cta h2{position:absolute;left:0;top:58px;width:976px;text-align:center;font-size:46px;font-weight:800;color:var(--white);letter-spacing:-.5px}
  .cta .kicker{position:absolute;left:0;top:118px;width:976px;text-align:center;font-size:15px;letter-spacing:6px;color:var(--bronze)}
  .cta p{position:absolute;left:88px;top:160px;width:800px;text-align:center;font-size:16px;line-height:33px;color:var(--white)}
  .btn-cta{position:absolute;left:369px;top:277px;width:238px;height:53px;background:var(--purple);border:1.5px solid var(--white);color:var(--white);font-size:14px;font-weight:700;border-radius:4px;display:flex;align-items:center;justify-content:center}

  /* footer */
  .footer-brand{position:absolute;left:110px;top:3990px;width:351px;text-align:center}
  .footer-brand .brand-dot{width:100px;height:100px;border-radius:50%;background:var(--bronze);margin:0 auto 30px}
  .footer-brand .brand-name{font-size:30px}
  .footer-brand .brand-tag{font-size:9px;letter-spacing:3.5px}
  .footer-links{position:absolute;left:552px;font-size:15.5px;color:#444}
  .footer-links span{margin-right:32px}
</style>
</head>
<body>

<header class="site-header">
  <span class="nav-link active" style="left:110px">HOME</span>
  <span class="nav-link" style="left:195px">ABOUT US</span>
  <span class="nav-link" style="left:307px">PRODUCTS</span>
  <span class="nav-link" style="left:775px">SERVICES</span>
  <span class="nav-link" style="left:883px">CONTACT US</span>
  <span class="btn-quote">GET A QUOTE</span>
</header>
<div class="brand-tab">
  <div class="brand-dot"></div>
  <div class="brand-name">NINTH BAY CAPITAL</div>
  <div class="brand-tag">YOUR NEXT CHAPTER STARTS NOW</div>
</div>

<section class="hero">
  <div class="hero-photo" role="img" aria-label="Portrait of a confident professional woman in a light blazer holding a folder"></div>
  <h1>WHERE DISCIPLINE<br>MEETS WEALTH</h1>
  <div class="eyebrow">YOUR NEXT CHAPTER STARTS NOW</div>
  <p>Structured financial strategy for athletes and entrepreneurs entering their next chapter — built for clarity, control, and long-term performance.</p>
  <span class="btn-strategy">START YOUR STRATEGY</span>
</section>

<section class="intro">
  <p class="intro-lead"><strong>Helping You Win Beyond the Season.</strong> Ninth Bay Capital helps athletes and entrepreneurs build disciplined, lasting financial systems—combining business precision, high-performance structure, and modern wealth strategy for long-term success.</p>

  <div class="pillars">
    <svg class="abs" style="left:0;top:0" width="1200" height="400" viewBox="0 0 1200 400">
      <g fill="none" stroke="var(--line)" stroke-width="5" stroke-linecap="round">
        <path d="M356,57 A156 156 0 1 0 387,234 L450,100 A156 156 0 0 1 730,96"/>
        <path d="M448,230 A156 156 0 0 0 732,234 L800,100 A156 156 0 1 1 841,286"/>
      </g>
      <g fill="var(--line)">
        <circle cx="356" cy="57" r="8"/>
        <circle cx="730" cy="96" r="8"/>
        <circle cx="448" cy="230" r="8"/>
        <circle cx="841" cy="286" r="8"/>
      </g>
    </svg>

    <div class="pillar" style="left:123px">
      <svg class="icon" width="40" height="30" viewBox="0 0 40 30"><path d="M2 15 C10 3 30 3 38 15 C30 27 10 27 2 15Z" fill="none" stroke="var(--bronze)" stroke-width="3"/><circle cx="20" cy="15" r="6" fill="var(--bronze)"/></svg>
      <h3>Clarity</h3>
      <p>Transparent, structured planning that removes uncertainty.</p>
    </div>
    <div class="pillar" style="left:471px">
      <svg class="icon" width="40" height="40" viewBox="0 0 40 40"><rect x="5" y="6" width="22" height="30" rx="2" fill="none" stroke="var(--bronze)" stroke-width="3"/><rect x="11" y="3" width="10" height="6" fill="var(--bronze)"/><path d="M10 16h12M10 22h8" stroke="var(--bronze)" stroke-width="3"/><circle cx="28" cy="28" r="6" fill="none" stroke="var(--bronze)" stroke-width="3"/><path d="M32 32l5 5" stroke="var(--bronze)" stroke-width="3"/></svg>
      <h3>Control</h3>
      <p>Systems and habits that support daily financial confidence.</p>
    </div>
    <div class="pillar" style="left:821px">
      <svg class="icon" width="44" height="34" viewBox="0 0 44 34"><rect x="2" y="14" width="8" height="16" fill="var(--bronze)"/><path d="M12 16h16a4 4 0 0 1 0 8H18M12 28h24l6-6" fill="none" stroke="var(--bronze)" stroke-width="3"/><circle cx="30" cy="8" r="6" fill="var(--bronze)"/></svg>
      <h3>Longevity</h3>
      <p>Strategies designed to build stability for the next generation.</p>
    </div>
  </div>
</section>

<section class="services">
  <h2 class="section-title" style="top:88px;color:var(--white)">WHAT WE OFFER</h2>
  <div class="section-kicker" style="top:156px;color:var(--white)">SERVICES</div>

  <div class="service-row" style="top:224px;height:189px">
    <span class="service-num" style="top:38px">01</span>
    <span class="service-name" style="top:8px">ASSESS</span>
    <p class="service-copy" style="top:49px;width:780px">Understand your current landscape: income, habits, contracts, identity, goals. Excepteur sint occaecat cupidatat non proident, sunt in culpa qui officia deserunt mollit anim id est laborum......Read More</p>
  </div>
  <div class="rule" style="top:413px"></div>

  <div class="service-row highlight" style="top:413px;height:231px">
    <span class="service-num" style="top:70px">02</span>
    <span class="service-name" style="top:50px">ARCHITECT</span>
    <p class="service-copy" style="top:90px;width:440px">Build disciplined systems for cash flow, planning, tax optimization, and investment pathways. Excepteur sint occaet in culpa qui officia deserunt.</p>
  </div>
  <div class="service-photo" role="img" aria-label="Hands sketching architectural plans on a drafting table"></div>

  <div class="service-row" style="top:644px;height:231px">
    <span class="service-num" style="top:70px">03</span>
    <span class="service-name" style="top:50px">ASCEND</span>
    <p class="service-copy" style="top:90px;width:790px">Evolve into long-term stability and generational prosperity with support designed to grow with you. Excepteur sint occaecat cupidatat non proident, sunt in culpa qui officia deserunt mollit anim id est laborum.</p>
  </div>
  <div class="rule" style="top:875px"></div>

  <span class="btn-more">VIEW MORE</span>
</section>

<section class="story">
  <h2 class="section-title" style="top:70px;color:var(--ink)">A NEW DIRECTION</h2>
  <div class="section-kicker" style="top:133px;color:#555">VISUAL STORY</div>
  <p class="lead">Ninth Bay bridges the worlds of performance, wealth, and wellness — helping athletes and entrepreneurs build lasting success on and off the field. It merges the discipline of sports, the structure of business, and the power of automation to create generational success.</p>

  <div class="story-mark">NINTH BAY CAPITAL</div>

  <div class="story-label right" style="left:0;width:345px;top:458px;color:var(--grey-label)">STRUCTURAL CLOSE-UPS</div>
  <div class="story-desc right" style="left:0;width:345px;top:496px">Lorem ipsum dolor<br>conctetur adipiscing elit</div>

  <div class="story-label" style="left:837px;top:458px;color:var(--pale-label)">OFF-FIELD ATHLETE</div>
  <div class="story-desc" style="left:839px;top:496px">Duis aute irure dolor in<br>reprehenderit in voluptate</div>

  <div class="story-label right" style="left:0;width:396px;top:718px;color:#9c8a72">FAMILY MOMENT</div>
  <div class="story-desc right" style="left:0;width:400px;top:754px">Eiusmod tempor incididunt ut<br>dolore magna aliqua</div>

  <div class="story-label" style="left:704px;top:750px;color:var(--pale-label)">ENTREPRENEUR AT WORK</div>
  <div class="story-desc" style="left:707px;top:780px">In voluptate velit esse cillum dolore<br>eu fugiat nulla pariatur.</div>
</section>

<section class="cta">
  <h2>YOUR NEXT QUARTER BEGINS TODAY</h2>
  <div class="kicker">CONTACT US</div>
  <p>Step into clarity, structure, and long-term wealth — built for athletes and leaders who demand more from their future. Excepteur sint occaecat cupidatat non proident, sunt in culpa qui officia exercitation ullamco laboris nisi ut aliquip ex ea commodo consequat deserunt mollit anim id est laborum.</p>
  <span class="btn-cta">START YOUR STRATEGY</span>
</section>

<footer>
  <div class="footer-brand">
    <div class="brand-dot"></div>
    <div class="brand-name">NINTH BAY CAPITAL</div>
    <div class="brand-tag">YOUR NEXT CHAPTER STARTS NOW</div>
  </div>
  <div class="footer-links" style="top:4036px"><span>HOME</span><span>ABOUT US</span><span>PRODUCTS</span><span>SERVICES</span><span>CONTACT US</span></div>
  <div class="footer-links" style="top:4082px"><span>PRIVACY POLICY</span><span>TERMS &amp; CONDITIONS</span><span>SUPPORT LINKS</span></div>
  <div class="footer-links" style="top:4125px">COPYRIGHTS@2025 NINTH BAY CAPITAL. ALL RIGHTS RESERVED</div>
</footer>

</body>
</html>
```